Road Construction Company needs business cards

We would like a new business card designed for our business.

We're a road construction company based in Qld, Australia.

Can the business card please have the following information on it.

Name: Warren Halbeck
Position: General Manager
Phone: 0472 915 348
Email: Warren.halbeck@tovrin.com.au
Address: 87 Marrow Ave, Pendlebay, QLD, 4023
Website: www.tovrin.com.au

Visually we'd like the card to be professional and simple.

Attached is our logo.

Our website is www.tovrin.com.au

Target Market(s)

Men aged 25-60

Contact Information for Business Card

As listed in project description

Font styles to use
Serif

Requirements
Must have
• Large logo on back of card

```html
<!DOCTYPE html>
<html lang="en">
<head>
<meta charset="utf-8">
<title>Tovrin Road Construction – Business Card</title>
<link rel="stylesheet" href="https://fonts.googleapis.com/css2?family=Noto+Serif:wght@400;700&display=swap">
<style>
  :root {
    --backdrop: #4a4a4a;
    --card: #171717;
    --edge: #0b5aad;
    --brand-blue: #0b5aad;
    --accent-blue: #36a3dc;
    --ink-light: #f2f2f2;
  }
  * { box-sizing: border-box; margin: 0; padding: 0; }
  html, body {
    width: 1200px;
    height: 801px;
    overflow: hidden;
    background: var(--backdrop);
    font-family: "Noto Serif", Georgia, serif;
  }
  .sheet {
    width: 1200px;
    height: 801px;
    display: flex;
    align-items: center;
    justify-content: center;
    gap: 40px;
  }
  .card {
    position: relative;
    width: 540px;
    height: 310px;
    background: var(--card);
    border: 2px solid var(--edge);
    border-radius: 18px;
    box-shadow: 0 18px 40px rgba(0,0,0,0.45);
    overflow: hidden;
  }

  /* Company name lockup */
  .wordmark {
    color: var(--brand-blue);
    font-weight: 700;
    line-height: 1;
  }
  .wordmark__name { display: block; }
  .wordmark__line { display: block; text-transform: uppercase; }

  /* Front */
  .card--front .wordmark {
    position: absolute;
    left: 34px;
    top: 34px;
  }
  .card--front .wordmark__name { font-size: 50px; letter-spacing: 2px; }
  .card--front .wordmark__line { font-size: 13px; letter-spacing: 7px; margin-top: 6px; }

  .person {
    position: absolute;
    left: 34px;
    top: 142px;
  }
  .person__name {
    color: var(--accent-blue);
    font-weight: 700;
    font-size: 25px;
    line-height: 1.1;
  }
  .person__role {
    color: var(--ink-light);
    font-size: 15px;
    margin-top: 3px;
  }
  .address {
    position: absolute;
    right: 34px;
    top: 40px;
    color: var(--ink-light);
    font-size: 14px;
    line-height: 1.45;
    text-align: right;
    font-style: normal;
  }
  .divider {
    position: absolute;
    left: 34px;
    right: 34px;
    top: 205px;
    height: 1.5px;
    background: var(--accent-blue);
  }
  .contacts {
    position: absolute;
    left: 34px;
    top: 218px;
    list-style: none;
    color: var(--ink-light);
    font-size: 14.5px;
  }
  .contacts__item {
    display: flex;
    align-items: center;
    gap: 8px;
    height: 23px;
  }
  .contacts__icon { width: 14px; height: 14px; fill: var(--accent-blue); flex: none; }

  /* Back */
  .card--back {
    display: flex;
    align-items: center;
    justify-content: center;
  }
  .card--back .wordmark { text-align: left; }
  .card--back .wordmark__name { font-size: 92px; letter-spacing: 4px; }
  .card--back .wordmark__line { font-size: 19px; letter-spacing: 10px; margin-top: 10px; }
</style>
</head>
<body>
<main class="sheet">

  <section class="card card--front" aria-label="Business card front">
    <div class="wordmark">
      <span class="wordmark__name">TOVRIN</span>
      <span class="wordmark__line">Road Construction</span>
    </div>

    <address class="address">87 Marrow Ave,<br>Pendlebay, QLD, 4023</address>

    <div class="person">
      <p class="person__name">Warren Halbeck</p>
      <p class="person__role">General Manager</p>
    </div>

    <div class="divider"></div>

    <ul class="contacts">
      <li class="contacts__item">
        <svg class="contacts__icon" viewBox="0 0 16 16" aria-hidden="true"><path d="M3.6 1.5l2.3 2.6-1.3 1.7c.9 2 2.6 3.7 4.6 4.6l1.7-1.3 2.6 2.3-1.2 2.2C7.3 14.3 1.7 8.7 1.4 3.7z"/></svg>
        <span>0472 915 348</span>
      </li>
      <li class="contacts__item">
        <svg class="contacts__icon" viewBox="0 0 16 16" aria-hidden="true"><path d="M1 3.5h14v9H1z M1.6 4l6.4 5 6.4-5" fill="none" stroke="#36a3dc" stroke-width="1.6"/></svg>
        <span>Warren.halbeck@tovrin.com.au</span>
      </li>
      <li class="contacts__item">
        <svg class="contacts__icon" viewBox="0 0 16 16" aria-hidden="true"><g fill="none" stroke="#36a3dc" stroke-width="1.4"><circle cx="8" cy="8" r="6.3"/><ellipse cx="8" cy="8" rx="2.8" ry="6.3"/><path d="M1.7 8h12.6"/></g></svg>
        <span>www.tovrin.com.au</span>
      </li>
    </ul>
  </section>

  <section class="card card--back" aria-label="Business card back">
    <div class="wordmark">
      <span class="wordmark__name">TOVRIN</span>
      <span class="wordmark__line">Road Construction</span>
    </div>
  </section>

</main>
</body>
</html>
```